Business Card Design

We need a business card designed for our new company. Prefer a black card with white logo & writing.

Contact Information for Business Card

Ted Galloway, address: 7-4812 Fernhollow Road, Abbotsford, BC, V3K 8R2, Office Phone: 604-712-3390, Cell: 604-947-2164, Email: ted@resinworkshub.ca

Colors

Designer to choose only greyscale colors for use in the design.

```html
<!DOCTYPE html>
<html lang="en">
<head>
<meta charset="utf-8">
<title>Resinworks Hub – Business Card</title>
<link href="https://fonts.googleapis.com/css2?family=Montserrat:wght@400;500;800&display=swap" rel="stylesheet">
<style>
  :root {
    --stage: #e4e4e4;
    --card-white: #ffffff;
    --card-black: #141414;
    --pattern-black: #1c1c1c;
    --ink: #111111;
    --ink-soft: #3a3a3a;
    --rule: #9a9a9a;
    --paper-text: #ffffff;
  }
  * { box-sizing: border-box; margin: 0; padding: 0; }
  html, body {
    width: 1200px; height: 786px; overflow: hidden;
    background: var(--stage);
    font-family: "Montserrat", sans-serif;
  }
  .stage {
    position: relative; width: 1200px; height: 786px;
    display: flex; align-items: center; justify-content: center; gap: 40px;
  }
  .card {
    position: relative; width: 540px; height: 309px;
    box-shadow: 0 10px 28px rgba(0,0,0,0.18);
    overflow: hidden;
  }
  .card-front { background: var(--card-white); color: var(--ink); }
  .card-back { background: var(--card-black); }

  .brand {
    position: absolute; left: 44px; top: 168px; transform: translateY(-50%);
    display: flex; align-items: center; gap: 10px;
    max-width: 200px;
  }
  .brand-mark { width: 14px; height: 14px; background: var(--ink); flex: none; }
  .brand-name {
    font-weight: 800; font-size: 22px; line-height: 1.05; letter-spacing: 0.5px;
    text-transform: uppercase; color: var(--ink);
  }
  .brand-name span { display: block; }

  .contact {
    position: absolute; left: 272px; top: 62px; width: 250px;
  }
  .contact-name { font-weight: 800; font-size: 19px; margin-left: 16px; }
  .contact-body {
    margin-top: 6px; border-left: 1px solid var(--rule); padding-left: 15px;
  }
  .contact-role { font-size: 12px; color: var(--ink-soft); margin-bottom: 12px; }
  .contact-list { list-style: none; }
  .contact-list li {
    display: flex; align-items: center; gap: 9px;
    font-size: 12.5px; line-height: 21px; color: var(--ink-soft);
  }
  .contact-list svg { width: 11px; height: 11px; flex: none; fill: var(--ink); }
  .contact-address {
    font-size: 12.5px; line-height: 17px; color: var(--ink-soft);
    margin: 4px 0 0 20px;
  }

  .back-pattern {
    position: absolute; inset: 0; background: var(--pattern-black);
  }
  .back-brand {
    position: absolute; right: 96px; top: 122px;
    display: flex; align-items: center; gap: 8px;
  }
  .back-brand .brand-mark { width: 10px; height: 10px; background: var(--paper-text); }
  .back-brand .brand-name { font-size: 15px; color: var(--paper-text); }
</style>
</head>
<body>
<main class="stage">
  <section class="card card-front" aria-label="Business card front">
    <div class="brand">
      <span class="brand-mark"></span>
      <span class="brand-name"><span>Resinworks</span><span>Hub</span></span>
    </div>
    <div class="contact">
      <h1 class="contact-name">Ted Galloway</h1>
      <div class="contact-body">
        <p class="contact-role">owner</p>
        <ul class="contact-list">
          <li><svg viewBox="0 0 24 24"><path d="M6.6 10.8a15 15 0 0 0 6.6 6.6l2.2-2.2c.3-.3.7-.4 1-.2 1.1.4 2.3.6 3.6.6.6 0 1 .4 1 1V20c0 .6-.4 1-1 1C10.6 21 3 13.4 3 4c0-.6.4-1 1-1h3.5c.6 0 1 .4 1 1 0 1.3.2 2.5.6 3.6.1.3 0 .7-.2 1z"/></svg>604-712-3390</li>
          <li><svg viewBox="0 0 24 24"><path d="M7 1h10a2 2 0 0 1 2 2v18a2 2 0 0 1-2 2H7a2 2 0 0 1-2-2V3a2 2 0 0 1 2-2zm0 3v14h10V4zm5 15.5a1.2 1.2 0 1 0 0 2.4 1.2 1.2 0 0 0 0-2.4z"/></svg>604-947-2164</li>
          <li><svg viewBox="0 0 24 24"><path d="M2 5h20v14H2zm2 2v.5l8 5 8-5V7zm0 2.9V17h16V9.9l-8 5z"/></svg>ted@resinworkshub.ca</li>
          <li><svg viewBox="0 0 24 24"><path d="M12 2a10 10 0 1 0 0 20 10 10 0 0 0 0-20zm6.9 6h-3a15 15 0 0 0-1.3-3.9A8 8 0 0 1 18.9 8zM12 4c.8 1.2 1.5 2.5 1.9 4h-3.8c.4-1.5 1.1-2.8 1.9-4zM4.3 14a8 8 0 0 1 0-4h3.4a16 16 0 0 0 0 4zm.8 2h3a15 15 0 0 0 1.3 3.9A8 8 0 0 1 5.1 16zm3-8h-3a8 8 0 0 1 4.3-3.9A15 15 0 0 0 8.1 8zM12 20c-.8-1.2-1.5-2.5-1.9-4h3.8c-.4 1.5-1.1 2.8-1.9 4zm2.3-6H9.7a14 14 0 0 1 0-4h4.6a14 14 0 0 1 0 4zm.3 5.9a15 15 0 0 0 1.3-3.9h3a8 8 0 0 1-4.3 3.9zm1.7-5.9a16 16 0 0 0 0-4h3.4a8 8 0 0 1 0 4z"/></svg>www.resinworkshub.ca</li>
        </ul>
        <p class="contact-address">7-4812 Fernhollow Road,<br>Abbotsford, BC, V3K 8R2</p>
      </div>
    </div>
  </section>

  <section class="card card-back" aria-label="Business card back">
    <div class="back-pattern" role="img" aria-label="Repeating tone-on-tone brand pattern across the black card"></div>
    <div class="back-brand">
      <span class="brand-mark"></span>
      <span class="brand-name">Resinworks Hub</span>
    </div>
  </section>
</main>
</body>
</html>
```